Landscape Construction and Design Company

We are a landscape construction and design company from New Jersey. We design and install landscapes and hardscapes for residential properties. The name of the company is Belwick's Landscape and Design LLC. We specialize mostly in planting trees and stone work, some water features. We would like to see design themes that include a tree or trees and a stone walkway or wall. We like earth tone colors. We like traditional to modern designs.

Target Market(s)

Homeowners

Industry/Entity Type

Landscape

Contact Information for Business Card

Nature themed design, earth tone colors, space for company name, address, phone numbers, email and website address

Logo Text

No text

Font styles to use
Serif

Colors

Designer to choose colors to be used in the design.

Requirements
Must have
• A tree or trees, similar to the ones uploaded in my supporting images
Nice to have
• I like trees similar to those in my uploaded supporting images. I like artistic, nature theme, earth tone colors
Should not have
• Pictures of real landscapes, cartoon looking logo or objects

```html
<!DOCTYPE html>
<html lang="en">
<head>
<meta charset="utf-8">
<title>Belwick's Landscape and Design LLC – Business Card</title>
<link rel="stylesheet" href="https://fonts.googleapis.com/css2?family=Cinzel:wght@400&family=Lato:wght@400&display=swap">
<style>
  :root {
    --backdrop: #9b9b9b;
    --card-white: #ffffff;
    --leaf-green: #5f9e2a;
    --leaf-light: #8cbf4a;
    --field-green: #6aa32e;
    --bark-red: #6b1a1a;
    --rule-grey: #9a9a9a;
    --ink-white: #ffffff;
  }
  * { margin: 0; padding: 0; box-sizing: border-box; }
  html, body { width: 1200px; height: 900px; overflow: hidden; }
  body { background: var(--backdrop); position: relative; font-family: "Lato", Arial, sans-serif; }

  .card {
    position: absolute;
    top: 306px;
    width: 439px;
    height: 271px;
    border-radius: 10px;
    overflow: hidden;
  }
  .card--front { left: 149px; background: var(--card-white); }
  .card--back { left: 609px; background: var(--field-green); }

  /* front: brand block */
  .brand-mark {
    position: absolute;
    left: 88px; top: 70px;
    width: 56px; height: 56px;
    border-radius: 50%;
    background: var(--leaf-light);
  }
  .brand-name {
    position: absolute;
    left: 20px; top: 170px;
    width: 192px;
    text-align: center;
    font-family: "Cinzel", Georgia, serif;
    font-weight: 400;
    color: var(--leaf-green);
    line-height: 1;
  }
  .brand-name__main { display: block; font-size: 29px; letter-spacing: 1px; }
  .brand-name__sub { display: block; font-size: 10.5px; margin-top: 6px; letter-spacing: 0.6px; }

  .divider {
    position: absolute;
    left: 227px; top: 76px;
    width: 1px; height: 121px;
    background: var(--rule-grey);
  }

  /* front: contact block */
  .contact { position: absolute; left: 243px; top: 70px; color: var(--bark-red); }
  .contact__name {
    font-family: "Cinzel", Georgia, serif;
    font-size: 16px; color: var(--leaf-green); letter-spacing: 0.3px; line-height: 1.1;
  }
  .contact__role { font-size: 11px; margin-top: 2px; letter-spacing: 0.2px; }
  .contact__lines { list-style: none; margin-top: 12px; }
  .contact__lines li { display: flex; align-items: center; font-size: 11.5px; height: 17px; }
  .contact__lines svg { width: 9px; height: 9px; margin-right: 4px; fill: var(--leaf-green); }
  .contact__address { font-size: 11.5px; line-height: 14px; margin-top: 7px; }

  /* back */
  .leaf-field {
    position: absolute; inset: 0;
    background: radial-gradient(ellipse at 55% 40%, #93c65a 0%, #78b23d 45%, var(--field-green) 100%);
  }
  .back-name {
    position: absolute;
    left: 0; right: 0; top: 102px;
    text-align: center;
    font-family: "Cinzel", Georgia, serif;
    font-weight: 400;
    color: var(--ink-white);
    line-height: 1;
  }
  .back-name__main { display: block; font-size: 44px; letter-spacing: 2px; }
  .back-name__sub { display: block; font-size: 15px; margin-top: 4px; letter-spacing: 1px; }
</style>
</head>
<body>

<section class="card card--front">
  <div class="brand-mark"></div>
  <div class="brand-name">
    <span class="brand-name__main">BELWICK'S</span>
    <span class="brand-name__sub">LANDSCAPE AND DESIGN LLC</span>
  </div>

  <div class="divider"></div>

  <div class="contact">
    <p class="contact__name">MARCUS HALE</p>
    <p class="contact__role">MANAGING DIRECTOR</p>
    <ul class="contact__lines">
      <li><svg viewBox="0 0 10 10" aria-hidden="true"><path d="M1 3 Q5 0 9 3 L8 4.5 L6.5 3.8 L6.5 3 Q5 2.5 3.5 3 L3.5 3.8 L2 4.5 Z M2 5 H8 V9 H2 Z"/></svg>444 555 7193</li>
      <li><svg viewBox="0 0 10 10" aria-hidden="true"><path d="M0.5 2 H9.5 V8 H0.5 Z M1 2.5 L5 5.5 L9 2.5" stroke="#fff" stroke-width="0.8"/></svg>INFO@BELWICKLAND.COM</li>
      <li><svg viewBox="0 0 10 10" aria-hidden="true"><circle cx="5" cy="5" r="4.5"/></svg>WWW.BELWICKLAND.COM</li>
    </ul>
    <p class="contact__address">218, ORCHARD LANE,<br>MILLBROOK NJ, 07046</p>
  </div>
</section>

<section class="card card--back">
  <div class="leaf-field" role="img" aria-label="Overlapping green leaves on branches filling the card"></div>
  <div class="back-name">
    <span class="back-name__main">BELWICK'S</span>
    <span class="back-name__sub">LANDSCAPE AND DESIGN LLC</span>
  </div>
</section>

</body>
</html>
```